Website for an electrical contractor :)

We are after a web site which can show pictures of our jobs and our capability in a professional, creative and easily understood way.

----- Brightvale Electrical ------

We really want a visually good looking website with three sections

Section one:
'Completed projects'
We have a few pictures of jobs which we've completed and would like to show off with a brief description. (see uploads)

Section two:
'Our capabilities'
Just a list of what services we offer

Section three:
We would like a 'contact us' section which people can send us a short msg and upload a file for plans to be able to send to us. We would need their name, phone number and email details. We would also need a short privacy policy saying 'we do not disclose information to third parties'.
We also want to display our contact number and postal address

Good luck :)

Target Market(s)

Adults 25 years+
Business owners
Builders
Real estate agents

Industry/Entity Type

Electrical

Colors

Designer to choose colors to be used in the design.

Requirements
Must have
• Visually appealing
Easy to understand
In the 'Completed projects' section, must have a list for each project we do i can upload pictures for it.

```html
<!DOCTYPE html>
<html lang="en">
<head>
<meta charset="utf-8">
<title>Brightvale Electrical</title>
<link href="https://fonts.googleapis.com/css2?family=Open+Sans:wght@700&family=Roboto+Condensed:wght@400;700&display=swap" rel="stylesheet">
<style>
  :root {
    --red: #e31e24;
    --ink: #222222;
    --body: #333333;
    --white: #ffffff;
    --btn-dark: #2f3436;
    --sky: #4a82c6;
    --haze: #b8c4cc;
    --concrete: #a9a8a2;
    --shade: #6d6c68;
    --sand: #d9c8a9;
  }
  * { margin: 0; padding: 0; box-sizing: border-box; }
  html, body {
    width: 1200px; height: 700px; overflow: hidden;
    background: var(--white);
    font-family: "Roboto Condensed", Arial, sans-serif;
    color: var(--body);
  }
  .page { position: relative; width: 1200px; height: 700px; }

  .site-header { position: absolute; top: 0; left: 0; width: 1200px; height: 68px; background: var(--white); }
  .brand {
    position: absolute; left: 208px; top: 14px;
    display: flex; align-items: center; gap: 10px;
    font-family: "Roboto Condensed", Arial, sans-serif;
    font-weight: 400; font-size: 30px; color: var(--ink); letter-spacing: -0.3px;
  }
  .brand-dot { width: 20px; height: 20px; border-radius: 50%; background: var(--red); }
  .main-nav { position: absolute; top: 30px; left: 660px; display: flex; gap: 40px; }
  .main-nav a { font-size: 16px; color: var(--ink); text-decoration: none; line-height: 22px; }
  .main-nav a.is-active { border-bottom: 1.5px solid var(--ink); }

  .hero {
    position: absolute; top: 68px; left: 0; width: 1200px; height: 396px;
    background: linear-gradient(180deg, var(--sky) 0%, var(--haze) 22%, var(--concrete) 45%, var(--shade) 62%, var(--concrete) 78%, var(--sand) 86%, var(--sand) 100%);
  }
  .hero-content { position: absolute; left: 199px; top: 82px; width: 300px; color: var(--white); }
  .hero-title {
    font-family: "Open Sans", Arial, sans-serif; font-weight: 700;
    font-size: 33px; line-height: 39px; letter-spacing: 0.3px;
    text-shadow: 0 2px 4px rgba(0,0,0,0.45);
  }
  .hero-lead { margin-top: 8px; font-size: 15px; line-height: 25px; text-shadow: 0 1px 3px rgba(0,0,0,0.5); }
  .hero-actions { position: absolute; left: 198px; top: 226px; display: flex; gap: 16px; }
  .btn {
    height: 46px; display: flex; align-items: center; justify-content: center;
    font-family: "Open Sans", Arial, sans-serif; font-weight: 700; font-size: 15px;
    color: var(--white); text-decoration: none; border-radius: 3px;
  }
  .btn-primary { width: 119px; background: var(--btn-dark); }
  .btn-outline { width: 122px; border: 2px solid var(--white); }

  .features { position: absolute; top: 484px; left: 0; width: 1200px; }
  .feature { position: absolute; top: 0; width: 240px; text-align: center; }
  .feature-icon { display: block; margin: 0 auto; width: 62px; height: 62px; }
  .feature-title { margin-top: 14px; font-weight: 700; font-size: 21px; color: var(--ink); line-height: 26px; }
  .feature-text { margin-top: 8px; font-size: 12.5px; line-height: 23px; color: var(--body); padding: 0 12px; }
</style>
</head>
<body>
<div class="page">
  <header class="site-header">
    <div class="brand"><span class="brand-dot"></span>Brightvale Electrical</div>
    <nav class="main-nav">
      <a href="#" class="is-active">Home</a>
      <a href="#">Projects</a>
      <a href="#">Services</a>
      <a href="#">Contact us</a>
    </nav>
  </header>

  <section class="hero" role="img" aria-label="Photo of a completed concrete tilt-up commercial building with steel awnings and a white work van on a sandy site under blue sky">
    <div class="hero-content">
      <h1 class="hero-title">Super Long Awesome Tagline</h1>
      <p class="hero-lead">Lorem ipsum dolor sit amet, consectetur adipiscing elit. MLorem ipsum dolor sit.</p>
    </div>
    <div class="hero-actions">
      <a href="#" class="btn btn-primary">Projects</a>
      <a href="#" class="btn btn-outline">What we do</a>
    </div>
  </section>

  <section class="features">
    <article class="feature" style="left:206px">
      <svg class="feature-icon" viewBox="0 0 62 62" aria-hidden="true">
        <circle cx="31" cy="31" r="27" fill="none" stroke="var(--red)" stroke-width="5"/>
        <path d="M8 24 Q31 34 54 24 M12 44 Q34 30 50 46 M22 6 Q20 34 40 57 M44 8 Q30 30 20 56" fill="none" stroke="var(--red)" stroke-width="3.5"/>
      </svg>
      <h2 class="feature-title">Strategic</h2>
      <p class="feature-text">Lorem ipsum dolor sit amet, consectetur adipiscing elit. MLorem ipsum dolor sit amet, consectetur adipiscing elit. Morbi sagittis varius odio vel interdum.</p>
    </article>
    <article class="feature" style="left:481px">
      <svg class="feature-icon" viewBox="0 0 62 62" aria-hidden="true">
        <path d="M16 12 A26 26 0 1 1 10 48" fill="none" stroke="var(--red)" stroke-width="5"/>
        <polygon points="6,6 22,8 10,20" fill="var(--red)"/>
        <path d="M31 16 V33 H43" fill="none" stroke="var(--red)" stroke-width="5"/>
        <circle cx="6" cy="32" r="2.5" fill="var(--red)"/>
        <circle cx="8" cy="41" r="2.5" fill="var(--red)"/>
        <circle cx="5" cy="24" r="2.5" fill="var(--red)"/>
      </svg>
      <h2 class="feature-title">Efficient</h2>
      <p class="feature-text">Lorem ipsum dolor sit amet, consectetur adipiscing elit. MLorem ipsum dolor sit amet, consectetur adipiscing elit. Morbi sagittis varius odio vel interdum.</p>
    </article>
    <article class="feature" style="left:756px">
      <svg class="feature-icon" viewBox="0 0 62 62" aria-hidden="true">
        <path d="M31 2 L54 10 V30 C54 46 43 55 31 60 C19 55 8 46 8 30 V10 Z" fill="var(--red)"/>
        <path d="M20 31 L28 39 L43 24" fill="none" stroke="var(--white)" stroke-width="5.5"/>
      </svg>
      <h2 class="feature-title">Safe</h2>
      <p class="feature-text">Lorem ipsum dolor sit amet, consectetur adipiscing elit. MLorem ipsum dolor sit amet, consectetur adipiscing elit. Morbi sagittis varius odio vel interdum.</p>
    </article>
  </section>
</div>
</body>
</html>
```